Pinecrest Capital Group - Company Envelopes

I am looking for a graphic designer to create a bespoke envelope for my company use, which I can then have printed at scale. The envelope should be of standard size and shape, but Matt black in colour, with semi-thick vertical gloss (shiny) lines going from left to right, but must stop to the right of the envelope, leaving a Matt black line with enough space for a stamp in the top right corner. The back of the envelope should be full Matt black.

Requirements
Must have
• Must be as described in brief
Should not have
• No other colours - Just Matt and Gloss Black

```html
<!DOCTYPE html>
<html lang="en">
<head>
<meta charset="utf-8">
<title>Pinecrest Capital Group – Company Envelopes</title>
<style>
  :root {
    --backdrop: #c1c1c1;
    --matt-black: #2b2b2b;
    --matt-black-deep: #232323;
    --gloss-top: #8a8a8a;
    --gloss-bottom: #3a3a3a;
    --gloss-edge: #1c1c1c;
    --flap-line: #d9d9d9;
  }
  html, body {
    margin: 0;
    padding: 0;
    width: 1200px;
    height: 895px;
    overflow: hidden;
    background: var(--backdrop);
  }
  .canvas {
    position: relative;
    width: 1200px;
    height: 895px;
    background: var(--backdrop);
  }
  .envelope {
    position: absolute;
    background: var(--matt-black);
    box-shadow: -6px 8px 18px rgba(0, 0, 0, 0.18);
    overflow: hidden;
  }
  .envelope--back {
    left: 285px;
    top: 135px;
    width: 629px;
    height: 275px;
  }
  .envelope__flap {
    position: absolute;
    left: 0;
    top: 0;
    width: 629px;
    height: 102px;
  }
  .envelope--front {
    left: 286px;
    top: 487px;
    width: 627px;
    height: 272px;
    background: var(--matt-black-deep);
  }
  .gloss-stripe {
    position: absolute;
    top: 0;
    width: 24.5px;
    height: 100%;
    background: linear-gradient(180deg, var(--gloss-top) 0%, var(--gloss-top) 45%, var(--gloss-bottom) 100%);
  }
  .gloss-stripe--1 { left: 0; }
  .gloss-stripe--2 { left: 48.2px; }
  .gloss-stripe--3 { left: 96.4px; background: linear-gradient(180deg, var(--gloss-top) 0%, var(--gloss-top) 35%, var(--gloss-bottom) 100%); }
  .gloss-stripe--4 { left: 144.6px; background: linear-gradient(180deg, var(--gloss-top) 0%, var(--gloss-top) 25%, var(--gloss-bottom) 100%); }
  .gloss-stripe--5 { left: 192.8px; background: linear-gradient(180deg, var(--gloss-top) 0%, var(--gloss-top) 15%, var(--gloss-edge) 100%); }
  .stamp-area {
    position: absolute;
    left: 531px;
    top: 18px;
    width: 77px;
    height: 77px;
    background: linear-gradient(135deg, #8c8c8c 0%, #3a3a3a 40%, #121212 55%, #101010 100%);
  }
</style>
</head>
<body>
  <main class="canvas">
    <section class="envelope envelope--back" aria-label="Envelope back, full matt black">
      <svg class="envelope__flap" viewBox="0 0 629 102" aria-hidden="true">
        <path d="M0.5 1 L628.5 1 M0.5 1 L20 75 Q26 100 50 100 L579 100 Q603 100 609 75 L628.5 1"
              fill="none" stroke="var(--flap-line)" stroke-width="0.8"/>
      </svg>
    </section>

    <section class="envelope envelope--front" aria-label="Envelope front, matt black with gloss stripes and stamp area">
      <div class="gloss-stripe gloss-stripe--1"></div>
      <div class="gloss-stripe gloss-stripe--2"></div>
      <div class="gloss-stripe gloss-stripe--3"></div>
      <div class="gloss-stripe gloss-stripe--4"></div>
      <div class="gloss-stripe gloss-stripe--5"></div>
      <div class="stamp-area" aria-label="Stamp area"></div>
    </section>
  </main>
</body>
</html>
```